RW Framewell Inc Business cards

We need business cards using our existing logo but slightly modified. Right now the logo says RW Loadbearing Masonry. We want to keep the RW part of the design, but replace the Structural Concrete portion with "FRAMEWELL". Please see the attached file.
Ideally this would be a blank template so we can add Different Names, titles, and phone numbers later.
On the one side we want only the logo and on the other side the detail. I'm attaching an example for you to see.
Please reach out with any other questions. Our address and other details will be given out once we find a design we like.

Target Market(s)

Construction Industry

```html
<!DOCTYPE html>
<html lang="en">
<head>
<meta charset="utf-8">
<title>RW Framewell Inc – Business Cards</title>
<link href="https://fonts.googleapis.com/css2?family=Montserrat:wght@600&family=Roboto:wght@400;700&display=swap" rel="stylesheet">
<style>
  :root {
    --page: #3a3a3c;
    --card: #1f1f21;
    --card-edge: #2a2a2c;
    --blue: #3a72c4;
    --white: #f2f2f2;
    --grey-logo: #6d6d70;
  }
  * { margin: 0; padding: 0; box-sizing: border-box; }
  html, body { width: 799px; height: 1200px; overflow: hidden; }
  body {
    background: var(--page);
    font-family: "Roboto", Arial, sans-serif;
    position: relative;
  }
  .card {
    position: absolute;
    left: 80px;
    width: 640px;
    height: 366px;
    background: var(--card);
    border: 1px solid var(--card-edge);
    border-radius: 6px;
    overflow: hidden;
    box-shadow: 0 18px 40px rgba(0,0,0,0.45);
  }
  .card--front { top: 150px; }
  .card--back  { top: 690px; }

  .wordmark {
    font-family: "Montserrat", Arial, sans-serif;
    font-weight: 600;
    letter-spacing: 0.16em;
    white-space: nowrap;
  }
  .card--front .wordmark {
    position: absolute;
    left: 0; right: 0; top: 160px;
    text-align: center;
    font-size: 40px;
    color: var(--grey-logo);
  }

  .accent-arc {
    position: absolute;
    left: -22px; top: 34px;
    width: 44px; height: 44px;
    border-radius: 50%;
    background: var(--blue);
  }
  .person { position: absolute; left: 40px; top: 36px; }
  .person__name { font-size: 22px; font-weight: 700; color: var(--blue); }
  .person__title { font-size: 15px; color: var(--white); margin-top: 4px; }

  .contact {
    position: absolute; left: 40px; top: 118px;
    list-style: none;
  }
  .contact li {
    display: flex; align-items: center;
    font-size: 15px; color: var(--white);
    height: 24px;
  }
  .contact svg { width: 13px; height: 13px; margin-right: 14px; fill: var(--blue); }

  .rule {
    position: absolute; height: 1px; background: var(--blue);
  }
  .rule--contact { left: 40px; top: 206px; width: 560px; }
  .rule--address { left: 380px; top: 322px; width: 220px; }

  .card--back .wordmark {
    position: absolute; right: 40px; top: 72px;
    font-size: 30px; color: var(--blue);
  }
  .address {
    position: absolute; right: 40px; top: 252px;
    text-align: right; font-size: 15px; line-height: 1.5;
    color: var(--white); font-style: normal;
  }
</style>
</head>
<body>
  <section class="card card--front" aria-label="Business card front">
    <div class="wordmark">RW FRAMEWELL</div>
  </section>

  <section class="card card--back" aria-label="Business card back">
    <span class="accent-arc"></span>
    <div class="person">
      <div class="person__name">Dana RW Miller</div>
      <div class="person__title">Managing Director</div>
    </div>
    <ul class="contact">
      <li>
        <svg viewBox="0 0 24 24" aria-hidden="true"><path d="M6.6 10.8a15 15 0 0 0 6.6 6.6l2.2-2.2c.3-.3.7-.4 1-.2 1.1.4 2.3.6 3.6.6.6 0 1 .4 1 1V20c0 .6-.4 1-1 1A17 17 0 0 1 3 4c0-.6.4-1 1-1h3.5c.6 0 1 .4 1 1 0 1.3.2 2.5.6 3.6.1.3 0 .7-.2 1z"/></svg>
        555-201-4470
      </li>
      <li>
        <svg viewBox="0 0 24 24" aria-hidden="true"><path d="M2 5h20v14H2z M2 5l10 8 10-8" fill="none" stroke="#3a72c4" stroke-width="2.4"/></svg>
        dana@rwframewell.com
      </li>
      <li>
        <svg viewBox="0 0 24 24" aria-hidden="true"><circle cx="12" cy="12" r="10"/></svg>
        www.rwframewell.com
      </li>
    </ul>
    <span class="rule rule--contact"></span>

    <div class="wordmark">RW FRAMEWELL</div>

    <address class="address">88 Timberline Rd., Oak Falls,<br>Nevada, US 889012</address>
    <span class="rule rule--address"></span>
  </section>
</body>
</html>
```